Corvane Capital Business Cards

These are professional business cards that are for my family office.
Put fake emails and phone numbers as of now until I finalize those components. This family office controls my families investments, assets, and future. The cards should be professional.
..
.
.
.
I just uploaded another variation of a logo I would like to see as a business card to I am inbeteen which logo to use

Target Market(s)

business

Industry/Entity Type

business

Contact Information for Business Card

Professional, wealth related, finance related.

Requirements
Must have
• Logo

```html
<!DOCTYPE html>
<html lang="en">
<head>
<meta charset="utf-8">
<title>Corvane Capital Business Cards</title>
<link href="https://fonts.googleapis.com/css2?family=Playfair+Display:wght@400;500&family=Poppins:wght@400&display=swap" rel="stylesheet">
<style>
  :root {
    --stage: #808080;
    --paper: #ffffff;
    --ink: #111111;
    --night: #131313;
    --gold: #c6ad6e;
  }
  html, body {
    margin: 0;
    padding: 0;
    width: 1093px;
    height: 1200px;
    overflow: hidden;
    background: var(--stage);
  }
  .card {
    position: absolute;
    left: 264px;
    width: 578px;
    height: 356px;
    border-radius: 26px;
    overflow: hidden;
    box-sizing: border-box;
  }
  .card::after {
    content: "";
    position: absolute;
    left: 0; right: 0; bottom: 0;
    height: 7px;
    background: var(--gold);
  }
  .card-front { top: 226px; background: var(--paper); }
  .card-back { top: 621px; background: var(--night); }

  .holder {
    position: absolute;
    left: 26px;
    top: 44px;
  }
  .holder-name {
    margin: 0;
    font-family: "Playfair Display", serif;
    font-weight: 500;
    font-size: 21px;
    line-height: 1;
    color: var(--ink);
    letter-spacing: 0.2px;
  }
  .holder-name .surname { color: var(--gold); }
  .holder-role {
    margin: 2px 0 0;
    font-family: "Poppins", sans-serif;
    font-size: 16px;
    line-height: 1.2;
    color: var(--ink);
  }

  .brand {
    position: absolute;
    display: flex;
    flex-direction: column;
    align-items: center;
  }
  .brand-mark { background: var(--gold); }
  .brand-name {
    font-family: "Playfair Display", serif;
    font-weight: 400;
    white-space: nowrap;
    line-height: 1;
    letter-spacing: 1px;
  }
  .card-front .brand { left: 288px; top: 50px; width: 266px; }
  .card-front .brand-mark { width: 34px; height: 34px; margin-bottom: 22px; }
  .card-front .brand-name { font-size: 33px; color: var(--ink); }
  .card-back .brand { left: 0; right: 0; top: 118px; }
  .card-back .brand-mark { width: 44px; height: 44px; margin-bottom: 30px; }
  .card-back .brand-name { font-size: 40px; color: var(--gold); }

  .contact-list {
    position: absolute;
    left: 26px;
    top: 258px;
    margin: 0;
    padding: 0;
    list-style: none;
    font-family: "Poppins", sans-serif;
    font-size: 17px;
    color: var(--ink);
  }
  .contact-list li {
    display: flex;
    align-items: center;
    height: 21px;
  }
  .contact-icon {
    width: 15px;
    height: 15px;
    margin-right: 7px;
    flex: none;
  }
  .address {
    position: absolute;
    right: 23px;
    top: 279px;
    margin: 0;
    font-family: "Poppins", sans-serif;
    font-style: normal;
    font-size: 17px;
    line-height: 21px;
    text-align: right;
    color: var(--ink);
  }
</style>
</head>
<body>
  <section class="card card-front" aria-label="Business card front">
    <div class="holder">
      <h1 class="holder-name">ADRIAN <span class="surname">HALE</span></h1>
      <p class="holder-role">Managing Director</p>
    </div>

    <div class="brand">
      <span class="brand-mark"></span>
      <span class="brand-name">CORVANE CAPITAL</span>
    </div>

    <ul class="contact-list">
      <li>
        <svg class="contact-icon" viewBox="0 0 16 16" aria-hidden="true">
          <path d="M3.5 1.5l2.3 2.6-1.2 1.6c.9 2 2.4 3.5 4.4 4.4l1.6-1.2 2.6 2.3-1.4 2.3C6.9 13.2 2.8 9.1 1.5 4.1z" fill="none" stroke="#c6ad6e" stroke-width="1.4" stroke-linejoin="round"/>
          <path d="M9.5 2.2a4.5 4.5 0 0 1 4.3 4.3M9.3 4.6a2.2 2.2 0 0 1 2.1 2.1" fill="none" stroke="#c6ad6e" stroke-width="1.3" stroke-linecap="round"/>
        </svg>
        044-321 654 987
      </li>
      <li>
        <svg class="contact-icon" viewBox="0 0 16 16" aria-hidden="true">
          <rect x="0.5" y="3" width="15" height="10" fill="#c6ad6e"/>
          <path d="M0.8 3.3L8 9l7.2-5.7M0.8 12.7l5-4.2M15.2 12.7l-5-4.2" fill="none" stroke="#ffffff" stroke-width="1"/>
        </svg>
        info@corvanemail.com
      </li>
      <li>
        <svg class="contact-icon" viewBox="0 0 16 16" aria-hidden="true">
          <g fill="none" stroke="#c6ad6e" stroke-width="1.2">
            <circle cx="8" cy="8" r="6.8"/>
            <ellipse cx="8" cy="8" rx="3" ry="6.8"/>
            <path d="M1.2 8h13.6M2.2 4.6h11.6M2.2 11.4h11.6"/>
          </g>
        </svg>
        www.corvanesite.com
      </li>
    </ul>

    <address class="address">421, Address line goes here<br>45452,Country Name</address>
  </section>

  <section class="card card-back" aria-label="Business card back">
    <div class="brand">
      <span class="brand-mark"></span>
      <span class="brand-name">CORVANE CAPITAL</span>
    </div>
  </section>
</body>
</html>
```